Luxury Toilet Rental Business. Tallowby Hire.

Tallowby Hire (the logo is in the uploaded files)
We RENT and SELL Luxury Trailer toilets.
- Show location, number, pricing, pictures.
- We have two stall trailers for rent AND 3 stall trailers
- We sell them too
- We want our phone number shown
- We are a local company
- Slogan: Brighten your gathering with Tallowby Hire. The Velvet Privy
- We want a pricing portion
- We want the sizes shown
- We want the different rates/ prices shown
- We do 1 day rentals
- We do 1 week rentals
- We want the service area. We serve Los Angeles County, Orange County, Riverside County, San Bernardino County, and Palm Desert.
- Our location is in Santa Ana California

Target Market(s)

Event planners, wedding planners, venue planners, concerts, events, gatherings.

Industry/Entity Type

Luxury Toilet Rentals

Number of Pages Required

1 page

Font styles to use
Serif
Sans Serif

Colors
EE7325
F08F49
F5BC92
FAE3D3
FDF4ED

Requirements
Must have
• Location, pricing, pictures, available areas. Our slogan.
Nice to have
• I like the idea of having tabs that show price, a tab that shows our contact information, pictures, event ideas, and where we service (the areas we'll go to)

```html
<!DOCTYPE html>
<html lang="en">
<head>
<meta charset="utf-8">
<title>Tallowby Hire — Luxury Trailer Toilets</title>
<link href="https://fonts.googleapis.com/css2?family=Audiowide&family=Poppins:wght@400;500;600&display=swap" rel="stylesheet">
<style>
:root{
  --orange:#EE7325;
  --orange-2:#F08F49;
  --orange-3:#F5BC92;
  --orange-4:#FAE3D3;
  --cream:#FDF4ED;
  --ink:#3b3b3b;
  --text:#4a4a4a;
  --nav:#4f4f4f;
  --light:#efefef;
  --white:#ffffff;
  --black:#111111;
}
*{box-sizing:border-box;margin:0;padding:0}
html,body{width:1200px;height:5063px;overflow:hidden}
body{font-family:"Poppins",Arial,sans-serif;color:var(--text);background:var(--white);position:relative}
.display{font-family:"Audiowide","Arial Black",sans-serif;text-transform:uppercase}
section,header,footer,nav{position:absolute;left:0;width:1200px}
.abs{position:absolute}
.accent{color:var(--orange)}
.btn{position:absolute;display:flex;align-items:center;justify-content:center;font-family:"Audiowide",sans-serif;text-transform:uppercase;font-size:13px;border-radius:3px;text-decoration:none}
.btn-fill{background:var(--orange);color:var(--white)}
.btn-line{background:var(--white);color:var(--orange);border:1.5px solid var(--orange-3)}
.photo{position:absolute}

/* header */
.site-header{top:0;height:94px;background:var(--white)}
.logo{position:absolute;display:flex;align-items:center;gap:10px;font-family:"Audiowide",sans-serif;color:var(--orange);text-transform:uppercase;white-space:nowrap}
.logo-square{width:14px;height:14px;background:var(--orange)}
.contact-chip{position:absolute;top:24px;display:flex;gap:12px;align-items:center}
.contact-chip .label{font-family:"Audiowide",sans-serif;color:var(--orange);font-size:13px;text-transform:uppercase}
.contact-chip .value{font-size:13px;color:var(--ink)}

/* nav */
.main-nav{top:94px;height:48px;background:var(--nav);display:flex;padding-left:165px}
.main-nav a{color:var(--white);font-size:13px;text-decoration:none;display:flex;align-items:center;padding:0 22px;height:48px}
.main-nav a.active{background:var(--orange)}

/* hero */
.hero{top:142px;height:601px;overflow:hidden}
.hero-title{left:47px;top:140px;color:var(--white);font-size:31px;line-height:43px;letter-spacing:1px}
.hero-text{left:59px;top:280px;width:400px;color:var(--white);font-size:14px;line-height:24px}

/* products */
.products{top:743px;height:745px;background:var(--white)}
.section-title{position:absolute;width:100%;text-align:center;font-size:30px;color:var(--ink);letter-spacing:1px}
.product-card{position:absolute;top:157px;width:380px;height:507px;background:var(--white);box-shadow:0 2px 10px rgba(0,0,0,.18)}
.product-card .photo{left:8px;top:8px;width:364px;height:258px}
.product-card h3{position:absolute;top:296px;width:100%;text-align:center;color:var(--orange);font-size:18px;line-height:23px;font-weight:400}
.product-card p{position:absolute;top:356px;left:30px;width:320px;text-align:center;font-size:13px;line-height:21px;color:var(--ink)}

/* about */
.about{top:1488px;height:592px;background:var(--light)}
.about-title{left:609px;top:110px;font-size:30px;color:var(--ink)}
.about-text{left:609px;width:460px;font-size:13px;line-height:25px;color:var(--text)}

/* service */
.where{top:2080px;height:485px;background:linear-gradient(180deg,var(--orange) 0%,var(--orange-2) 100%);overflow:hidden}
.where-title{top:82px;color:var(--white)}
.event-card{position:absolute;top:155px;width:230px;height:228px;background:var(--white);border-radius:6px;box-shadow:0 2px 8px rgba(0,0,0,.2);overflow:hidden}
.event-card .photo{left:4px;top:4px;width:222px;height:172px;border-radius:4px 4px 0 0}
.event-card span{position:absolute;bottom:18px;width:100%;text-align:center;font-weight:500;font-size:15px;color:var(--black)}

/* pricing */
.pricing{top:2565px;height:540px;background:var(--white)}
.price-card{position:absolute;top:59px;width:299px;height:397px;background:var(--white);box-shadow:0 2px 10px rgba(0,0,0,.18)}
.price-card .photo{left:6px;top:6px;width:287px;height:171px}
.price-card h3{position:absolute;top:206px;width:100%;text-align:center;font-size:15px;line-height:20px;color:var(--ink);font-weight:400}
.price-card .price{position:absolute;top:247px;width:100%;text-align:center;font-size:26px;color:var(--orange)}
.price-card p{position:absolute;top:288px;left:34px;width:231px;text-align:center;font-size:11px;line-height:17px;color:var(--ink)}

/* slogan */
.slogan{top:3105px;height:384px;overflow:hidden}
.slogan-text{top:150px;width:100%;text-align:center;color:var(--white);font-size:30px;line-height:41px;letter-spacing:1.5px}

/* service area */
.area{top:3489px;height:475px;background:var(--white)}
.area-list{font-size:18px;color:var(--black);display:flex;align-items:center;gap:4px}

/* contact */
.contact{top:3964px;height:621px;background:var(--light);overflow:hidden}
.field{position:absolute;background:var(--white);border:1.5px solid var(--ink);border-radius:3px;font-size:11px;color:var(--ink);display:flex;align-items:center;gap:8px;padding-left:14px}
.info-row{position:absolute;left:143px;display:flex;align-items:center;gap:14px;font-size:14px;color:var(--ink)}
.info-icon{width:40px;height:40px;flex:none;border-radius:50%;background:#e0e0e0;display:flex;align-items:center;justify-content:center}

/* footer */
.site-footer{top:4585px;height:478px;background:var(--black);color:var(--white)}
.footer-col{position:absolute;top:95px}
.footer-col h4{font-family:"Audiowide",sans-serif;font-weight:400;font-size:15px;text-transform:uppercase;margin-bottom:22px}
.footer-col li{list-style:none;font-size:13px;line-height:29.5px}
.social li{display:flex;align-items:center;gap:12px;font-size:14px;line-height:42px}
.social-dot{width:28px;height:28px;border-radius:50%;background:#e9e9e9}
.copyright{position:absolute;top:436px;width:100%;text-align:center;font-size:12px}
</style>
</head>
<body>

<header class="site-header">
  <div class="logo" style="left:189px;top:28px;font-size:27px">
    <span class="logo-square"></span>Tallowby Hire
  </div>
  <div class="contact-chip" style="left:511px">
    <svg width="40" height="40" viewBox="0 0 40 40"><rect x="3" y="10" width="34" height="24" fill="none" stroke="#EE7325" stroke-width="3"/><path d="M3 10 L20 24 L37 10" fill="none" stroke="#EE7325" stroke-width="3"/></svg>
    <div><div class="label">Email Us :</div><div class="value">info@tallowbyhire.example</div></div>
  </div>
  <div class="contact-chip" style="left:743px">
    <svg width="40" height="40" viewBox="0 0 40 40"><circle cx="20" cy="20" r="17" fill="none" stroke="#EE7325" stroke-width="3"/><path d="M13 11 l5 0 2 6 -3 2 c2 4 4 6 7 7 l2 -3 6 2 0 5 c-11 1 -20 -8 -19 -19z" fill="#EE7325"/></svg>
    <div><div class="label">Phone Number :</div><div class="value">+1 555 014 2290</div></div>
  </div>
</header>

<nav class="main-nav">
  <a class="active" href="#">Home</a>
  <a href="#">About Us</a>
  <a href="#">Where We Service</a>
  <a href="#">Service area</a>
  <a href="#">Pricing</a>
  <a href="#">Gallery</a>
  <a href="#">Event</a>
  <a href="#">Contact Us</a>
</nav>

<section class="hero">
  <div class="photo" role="img" aria-label="Grey two-door toilet trailer with steel steps parked in a paved yard" style="left:0;top:0;width:1200px;height:601px;background:linear-gradient(135deg,#bfc2c4 0%,#8f9396 45%,#6b6f72 100%)"></div>
  <svg class="abs" style="left:0;top:0" width="1200" height="601" viewBox="0 0 1200 601">
    <polygon points="0,0 700,0 520,601 0,601" fill="#F08F49" opacity="0.75"/>
    <polygon points="0,0 650,0 462,601 0,601" fill="#EE7325"/>
  </svg>
  <h1 class="abs display hero-title" style="font-weight:400">Welcome to<br>Tallowby Hire<br>Local Company</h1>
  <p class="abs hero-text">Lorem ipsum dolor sit amet, consectetur adipiscing elit, sed do eiusmod tempor incididunt ut labore et dolore magna aliqua.</p>
  <a class="btn btn-line" style="left:59px;top:371px;width:151px;height:39px;border:none">Day Rentals</a>
  <a class="btn btn-line" style="left:220px;top:371px;width:167px;height:39px;border:none">Week Rentals</a>
</section>

<section class="products">
  <h2 class="section-title display" style="top:72px;font-weight:400">Our <span class="accent">Products</span></h2>
  <article class="product-card" style="left:202px">
    <div class="photo" role="img" aria-label="Two stall toilet trailer photographed in a yard" style="background:linear-gradient(180deg,#c9cdd1 0%,#8d9196 55%,#a9acae 100%)"></div>
    <h3 class="display">Two Stall Trailers<br>Taliler : 7'x 8'</h3>
    <p>Lorem ipsum dolor sit amet, consectetur adipiscing elit, sed do eiusmod tempor incididunt ut labore et dolore magna aliqua.</p>
    <a class="btn btn-fill" style="left:97px;top:432px;width:96px;height:38px">Sell</a>
    <a class="btn btn-line" style="left:199px;top:432px;width:90px;height:38px">Rent</a>
  </article>
  <article class="product-card" style="left:619px">
    <div class="photo" role="img" aria-label="Three stall toilet trailer with blue steps in a yard" style="background:linear-gradient(180deg,#cbd0d4 0%,#878c91 55%,#a6a9ab 100%)"></div>
    <h3 class="display">3 Stall Trailers<br>Taliler : 7'x 14'</h3>
    <p>Lorem ipsum dolor sit amet, consectetur adipiscing elit, sed do eiusmod tempor incididunt ut labore et dolore magna aliqua.</p>
    <a class="btn btn-fill" style="left:95px;top:430px;width:96px;height:38px">Sell</a>
    <a class="btn btn-line" style="left:197px;top:430px;width:90px;height:38px">Rent</a>
  </article>
</section>

<section class="about">
  <div class="abs" style="left:134px;top:94px;width:266px;height:246px;border:3px solid var(--orange)"></div>
  <div class="abs" style="left:290px;top:250px;width:264px;height:246px;border:3px solid #8a8a8a"></div>
  <div class="photo" role="img" aria-label="Toilet trailer parked beside a building, video preview" style="left:151px;top:112px;width:384px;height:389px;background:linear-gradient(160deg,#a7a59d 0%,#7d7f80 50%,#9b9c98 100%)"></div>
  <svg class="abs" style="left:316px;top:277px" width="56" height="56" viewBox="0 0 56 56" aria-label="Play video"><circle cx="28" cy="28" r="27" fill="#EE7325" stroke="#ffffff" stroke-width="2"/><polygon points="23,18 38,28 23,38" fill="#ffffff"/></svg>
  <h2 class="abs about-title display" style="font-weight:400">About <span class="accent">Us</span></h2>
  <p class="abs about-text" style="top:170px">Lorem ipsum dolor sit amet, consectetur adipiscing elit, sed do eiusmod tempor incididunt ut labore et dolore magna aliqua. Quis ipsum suspendisse ultrices gravida. Risus commodo viverra maecenas accumsan lacus vel facilisis.</p>
  <p class="abs about-text" style="top:276px">Sed ut perspiciatis unde omnis iste natus error sit voluptatem accusantium doloremque laudantium, totam rem aperiam, eaque ipsa quae ab illo inventore veritatis et quasi architecto beatae vitae dicta sunt explicabo. Nemo enim ipsam voluptatem quia voluptas sit aspernatur aut odit aut fugit, sed quia consequuntur magni dolores eos qui ratione voluptatem sequi nesciunt.</p>
  <a class="btn btn-fill" style="left:609px;top:440px;width:138px;height:37px">Read More</a>
</section>

<section class="where">
  <svg class="abs" style="left:0;top:0" width="1200" height="485" viewBox="0 0 1200 485"><polygon points="700,485 1200,140 1200,485" fill="#F5BC92" opacity="0.25"/><polygon points="0,485 0,300 260,485" fill="#F5BC92" opacity="0.2"/></svg>
  <h2 class="section-title where-title display" style="font-weight:400">Where We Service</h2>
  <div class="event-card" style="left:120px"><div class="photo" role="img" aria-label="Construction site with cranes" style="background:linear-gradient(180deg,#7fb0dc,#c9a64a)"></div><span>Construction</span></div>
  <div class="event-card" style="left:364px"><div class="photo" role="img" aria-label="Outdoor wedding dinner under string lights" style="background:linear-gradient(180deg,#e0b35a,#4a3a22)"></div><span>Outdoor Weddings</span></div>
  <div class="event-card" style="left:609px"><div class="photo" role="img" aria-label="Crowd at a sports event" style="background:linear-gradient(180deg,#5a4a3c,#2a2420)"></div><span>Sport Events</span></div>
  <div class="event-card" style="left:853px"><div class="photo" role="img" aria-label="Outdoor movie event in a park at sunset" style="background:linear-gradient(180deg,#e8b650,#3e5a2a)"></div><span>Outdoor Events</span></div>
</section>

<section class="pricing">
  <h2 class="abs display" style="left:104px;top:168px;font-size:30px;color:var(--ink);font-weight:400">Our <span class="accent">Pricing</span></h2>
  <p class="abs" style="left:104px;top:221px;width:360px;font-size:13px;line-height:24px;color:var(--ink)">Lorem ipsum dolor sit amet, consectetur adipiscing elit, sed do eiusmod tempor incididunt ut labore et dolore magna aliqua. Quis ipsum suspendisse ultrices gravida.</p>
  <a class="btn btn-fill" style="left:104px;top:303px;width:98px;height:39px">Sell</a>
  <a class="btn btn-line" style="left:206px;top:303px;width:90px;height:39px">Rent</a>
  <article class="price-card" style="left:507px">
    <div class="photo" role="img" aria-label="Two stall toilet trailer" style="background:linear-gradient(180deg,#c9cdd1 0%,#8d9196 55%,#a9acae 100%)"></div>
    <h3 class="display">2Stall Trailers<br>Taliler : 7'x 8'</h3>
    <div class="price display">$85.00</div>
    <p>Lorem ipsum dolor sit amet, consectetur adipiscing elit, sed dolore magna aliqua.</p>
    <a class="btn btn-fill" style="left:110px;top:342px;width:80px;height:28px;font-size:11px">Sell</a>
  </article>
  <article class="price-card" style="left:827px">
    <div class="photo" role="img" aria-label="Three stall toilet trailer" style="background:linear-gradient(180deg,#cbd0d4 0%,#878c91 55%,#a6a9ab 100%)"></div>
    <h3 class="display">3 Stall Trailers<br>Taliler : 7'x 14'</h3>
    <div class="price display">$185.00</div>
    <p>Lorem ipsum dolor sit amet, consectetur adipiscing elit, sed dolore magna aliqua.</p>
    <a class="btn btn-fill" style="left:110px;top:342px;width:80px;height:28px;font-size:11px">Sell</a>
  </article>
</section>

<section class="slogan">
  <div class="photo" role="img" aria-label="Dimmed interior of a luxury restroom trailer with sink and toilet" style="left:0;top:0;width:1200px;height:384px;background:linear-gradient(90deg,#3a3a3a 0%,#5a5a5a 50%,#3e3e3e 100%)"></div>
  <h2 class="abs slogan-text display" style="font-weight:400">Brighten your gathering with<br>Tallowby Hire. The Velvet Privy</h2>
</section>

<section class="area">
  <h2 class="abs display" style="left:104px;top:128px;font-size:30px;color:var(--ink);font-weight:400">Service <span class="accent">Area</span></h2>
  <div class="abs area-list" style="left:104px;top:198px"><svg width="12" height="16" viewBox="0 0 12 16"><path d="M6 0a6 6 0 0 0-6 6c0 4 6 10 6 10s6-6 6-10a6 6 0 0 0-6-6z" fill="#EE7325"/><circle cx="6" cy="6" r="2.2" fill="#fff"/></svg>Los Angeles</div>
  <div class="abs area-list" style="left:104px;top:235px"><svg width="12" height="16" viewBox="0 0 12 16"><path d="M6 0a6 6 0 0 0-6 6c0 4 6 10 6 10s6-6 6-10a6 6 0 0 0-6-6z" fill="#EE7325"/><circle cx="6" cy="6" r="2.2" fill="#fff"/></svg>Orange County</div>
  <div class="abs area-list" style="left:104px;top:273px"><svg width="12" height="16" viewBox="0 0 12 16"><path d="M6 0a6 6 0 0 0-6 6c0 4 6 10 6 10s6-6 6-10a6 6 0 0 0-6-6z" fill="#EE7325"/><circle cx="6" cy="6" r="2.2" fill="#fff"/></svg>Riverside County</div>
  <div class="abs area-list" style="left:289px;top:196px"><svg width="12" height="16" viewBox="0 0 12 16"><path d="M6 0a6 6 0 0 0-6 6c0 4 6 10 6 10s6-6 6-10a6 6 0 0 0-6-6z" fill="#EE7325"/><circle cx="6" cy="6" r="2.2" fill="#fff"/></svg>Palm Desert</div>
  <div class="abs area-list" style="left:289px;top:233px"><svg width="12" height="16" viewBox="0 0 12 16"><path d="M6 0a6 6 0 0 0-6 6c0 4 6 10 6 10s6-6 6-10a6 6 0 0 0-6-6z" fill="#EE7325"/><circle cx="6" cy="6" r="2.2" fill="#fff"/></svg>San Bernardino</div>
  <div class="photo" role="img" aria-label="Map of the Southern California counties served" style="left:540px;top:68px;width:541px;height:299px;background:radial-gradient(ellipse at 55% 50%,#F08F49 0%,#F5BC92 60%,#ffffff 100%);border-radius:40px"></div>
</section>

<section class="contact">
  <div class="photo" role="img" aria-label="Faint city skyline silhouette" style="left:0;top:430px;width:1200px;height:191px;background:linear-gradient(180deg,rgba(220,220,220,0) 0%,#dcdcdc 100%)"></div>
  <h2 class="section-title display" style="top:82px;font-weight:400">Contact <span class="accent">Us</span></h2>
  <h3 class="abs display" style="left:143px;top:168px;font-size:16px;line-height:24px;color:var(--ink);font-weight:400">Let's make something<br>great together</h3>
  <p class="abs" style="left:143px;top:230px;width:330px;font-size:15px;line-height:24px;color:var(--ink)">Sed ut perspiciatis undomnisistenatus error sit voluptatem</p>
  <div class="info-row" style="top:297px"><span class="info-icon"><svg width="12" height="16" viewBox="0 0 12 16"><path d="M6 0a6 6 0 0 0-6 6c0 4 6 10 6 10s6-6 6-10a6 6 0 0 0-6-6z" fill="#444"/><circle cx="6" cy="6" r="2.2" fill="#e0e0e0"/></svg></span><span style="width:220px;line-height:22px">500 Tallowby Hire Lorem ipsum 94158</span></div>
  <div class="info-row" style="top:363px"><span class="info-icon"><svg width="16" height="16" viewBox="0 0 16 16"><path d="M2 1h4l1.5 4-2 1.5c1 2 2.5 3.5 4.5 4.5l1.5-2 4 1.5v4C8 15 1 8 2 1z" fill="#444"/></svg></span>+1 555 014 2290</div>
  <div class="info-row" style="top:421px"><span class="info-icon"><svg width="18" height="14" viewBox="0 0 18 14"><rect x="1" y="1" width="16" height="12" fill="none" stroke="#444" stroke-width="2"/><path d="M1 1l8 6 8-6" fill="none" stroke="#444" stroke-width="2"/></svg></span>info@tallowbyhire.example</div>

  <div class="field" style="left:533px;top:150px;width:251px;height:47px">&#128100;&#xFE0E; Frist Name</div>
  <div class="field" style="left:806px;top:150px;width:251px;height:47px">&#128100;&#xFE0E; Last Name</div>
  <div class="field" style="left:533px;top:219px;width:251px;height:47px">&#9993; Email</div>
  <div class="field" style="left:806px;top:219px;width:251px;height:47px">&#9742; Phone</div>
  <div class="field" style="left:533px;top:289px;width:524px;height:142px;align-items:flex-start;padding-top:14px">&#9993; Message</div>
  <a class="btn btn-fill" style="left:533px;top:443px;width:113px;height:39px">Submit</a>
</section>

<footer class="site-footer">
  <div class="footer-col" style="left:124px">
    <h4>Quick Links</h4>
    <ul>
      <li>&raquo;&nbsp; Home</li><li>&raquo;&nbsp; About Us</li><li>&raquo;&nbsp; Where We Service</li><li>&raquo;&nbsp; Service area</li><li>&raquo;&nbsp; Pricing</li><li>&raquo;&nbsp; Gallery</li><li>&raquo;&nbsp; Event</li><li>&raquo;&nbsp; Contact Us</li>
    </ul>
  </div>
  <div class="footer-col" style="left:322px">
    <h4>Contact Info</h4>
    <ul>
      <li style="line-height:22px;width:220px">&#9679; 500 Tallowby Hire Lorem ipsum 94158</li>
      <li style="margin-top:10px">&#9742; +1 555 014 2290</li>
      <li>&#9993; info@tallowbyhire.example</li>
    </ul>
  </div>
  <div class="footer-col social" style="left:586px">
    <h4>Follow Us</h4>
    <ul>
      <li><span class="social-dot"></span>Facefolio</li>
      <li><span class="social-dot"></span>Chirper</li>
      <li><span class="social-dot"></span>Linkwork</li>
      <li><span class="social-dot"></span>Pinboardly</li>
    </ul>
  </div>
  <div class="logo" style="left:774px;top:100px;font-size:30px">
    <span class="logo-square"></span>Tallowby Hire
  </div>
  <div class="copyright">&copy; 2024 Tallowby Hire | All Rights Reserved</div>
</footer>

</body>
</html>
```